Business Cards for new orthopaedic surgery practice

My husband and I are starting our own orthopaedic surgery practice. We are looking for a business card that is uniform, but one will have my name/title and the other will have his. You can just create one design with my name on it for now. But when I choose your design as the winning design I will ask that you add another copy with his name/title.

We are looking for classy, simple, elite all in one. We like dark blues/a little gold/yellow. Something that goes with our logo. We want our logo incorporated. Here is all the info you need:
Business name: RV Bone & Vitality Center
Location: 38517 North Willowmere Ave
Palmetto Ridge, FL 33408
Phone: 954-218-4063
Fax: 954-582-7341
Email: info@myrvbonecare.example

Names: Lydia Vance, M.D.
Board Certified Hand and Upper Extremity Surgeon

Ebo Dansu, M.D.
Board Certified Hip & Knee Replacement/General Orthopaedic Surgeon

Can decide what you want to put on the back. Maybe a slogan:
Grounded in Care. Centered on You

I am just going to upload our logo. The only thing is if we select you as the winning design, the location, and phone numbers may change. We will need your help to update that once fully solidified.

Industry/Entity Type

Medical

Contact Information for Business Card

Colors
0054AA
0677BA
7BADD7
CADEEF
E8F1F8
0094D4
00A9DD
6FCCEA
C7EBF8
E9F6FB

Requirements
Must have
• class, appeal,
Should not have
• We want to air on the side of masculine if we are looking at masculine vs. feminine feel. But we still want it classy, sophisticated, and something we will love

```html
<!DOCTYPE html>
<html lang="en">
<head>
<meta charset="utf-8">
<title>RV Bone &amp; Vitality Center — Business Card</title>
<link rel="stylesheet" href="https://fonts.googleapis.com/css2?family=Libre+Baskerville:wght@400;700&display=swap">
<style>
  :root {
    --navy: #1b2a52;
    --gold: #c9a04f;
    --white: #ffffff;
    --stage: #2e2f33;
    --ink: #1b2a52;
  }
  * { box-sizing: border-box; margin: 0; padding: 0; }
  html, body { width: 1200px; height: 801px; overflow: hidden; }
  body {
    background: var(--stage);
    font-family: "Libre Baskerville", Georgia, serif;
    position: relative;
  }
  .card {
    position: absolute;
    width: 540px;
    height: 309px;
    border-radius: 14px;
    overflow: hidden;
    box-shadow: 0 10px 24px rgba(0,0,0,.45);
  }
  .card--back {
    left: 40px; top: 246px;
    background: var(--navy);
    color: var(--white);
  }
  .card--front {
    left: 620px; top: 246px;
    background: var(--white);
    color: var(--ink);
  }
  .card__art { position: absolute; inset: 0; width: 100%; height: 100%; }

  /* back */
  .back-mark {
    position: absolute; left: 50%; top: 118px;
    transform: translate(-50%, -50%);
    width: 170px; text-align: center;
  }
  .back-mark__name {
    font-size: 18px; font-weight: 700; line-height: 1.4;
    letter-spacing: .03em; color: var(--white);
  }
  .slogan {
    position: absolute; left: 0; right: 0; top: 246px;
    text-align: center; font-size: 13px; letter-spacing: .08em; color: var(--white);
  }

  /* front */
  .identity { position: absolute; left: 32px; top: 44px; width: 300px; }
  .identity__name { font-size: 22px; font-weight: 700; letter-spacing: .02em; color: var(--navy); }
  .identity__title { font-size: 10px; margin-top: 6px; color: var(--navy); }
  .identity__rule { height: 1.5px; background: var(--gold); margin: 10px 0 12px; width: 300px; }
  .address { font-size: 11.5px; line-height: 1.6; color: var(--navy); }
  .contacts { list-style: none; margin-top: 8px; }
  .contacts li {
    display: flex; align-items: center; gap: 9px;
    font-size: 11.5px; line-height: 1.7; color: var(--navy);
  }
  .contacts svg { width: 12px; height: 12px; flex: none; }

  .front-mark {
    position: absolute; left: 370px; top: 28px;
    width: 140px; height: 140px;
    display: flex; align-items: center; justify-content: center; text-align: center;
  }
  .front-mark__name {
    position: relative; width: 100px;
    font-size: 13px; font-weight: 700; line-height: 1.4; color: var(--navy);
  }
  .front-mark svg { position: absolute; inset: 0; }

  .social { position: absolute; right: 30px; top: 196px; display: flex; gap: 6px; }
  .social span { width: 18px; height: 18px; border-radius: 50%; background: var(--white); }
</style>
</head>
<body>

<section class="card card--back" aria-label="Card back">
  <svg class="card__art" viewBox="0 0 540 309" aria-hidden="true">
    <circle cx="270" cy="118" r="96" fill="none" stroke="var(--gold)" stroke-width="1.6"/>
  </svg>
  <div class="back-mark">
    <p class="back-mark__name">RV Bone &amp; Vitality Center</p>
  </div>
  <p class="slogan">Grounded in Care. Centered on You</p>
</section>

<section class="card card--front" aria-label="Card front">
  <svg class="card__art" viewBox="0 0 540 309" preserveAspectRatio="none" aria-hidden="true">
    <path d="M0 284 C160 278 300 252 362 214 C414 184 456 178 540 170 L540 309 L0 309 Z" fill="var(--gold)"/>
    <path d="M0 288 C160 282 302 256 365 218 C417 188 458 182 540 174 L540 309 L0 309 Z" fill="var(--white)"/>
    <path d="M0 291 C162 286 304 259 368 221 C420 191 460 185 540 177 L540 309 L0 309 Z" fill="var(--navy)"/>
  </svg>

  <div class="identity">
    <h1 class="identity__name">LYDIA VANCE, M.D</h1>
    <p class="identity__title">Board Certified Hand and Upper Extremity Surgeon</p>
    <div class="identity__rule"></div>
    <p class="address">38517 North Willowmere Ave<br>Palmetto Ridge, FL 33408</p>
    <ul class="contacts">
      <li><svg viewBox="0 0 12 12"><path d="M2.5 1 L4.5 1 L5.3 3.4 L4 4.4 C4.6 5.8 6.2 7.4 7.6 8 L8.6 6.7 L11 7.5 L11 9.5 C11 10.3 10.3 11 9.5 11 C5 11 1 7 1 2.5 C1 1.7 1.7 1 2.5 1 Z" fill="var(--gold)"/></svg>954-218-4063</li>
      <li><svg viewBox="0 0 12 12"><rect x="3" y="1" width="6" height="3" fill="var(--gold)"/><rect x="1" y="4.5" width="10" height="4.5" rx="1" fill="var(--gold)"/><rect x="3" y="8" width="6" height="3" fill="var(--gold)"/></svg>954-218-4063</li>
      <li><svg viewBox="0 0 12 12"><rect x="1" y="2.5" width="10" height="7" fill="var(--gold)"/><path d="M1 2.5 L6 6.5 L11 2.5" fill="none" stroke="var(--white)" stroke-width="1"/></svg>info@myrvbonecare.example</li>
      <li><svg viewBox="0 0 12 12"><circle cx="6" cy="6" r="5" fill="none" stroke="var(--gold)" stroke-width="1.2"/><path d="M1 6 H11 M6 1 C3.5 3.5 3.5 8.5 6 11 M6 1 C8.5 3.5 8.5 8.5 6 11" fill="none" stroke="var(--gold)" stroke-width="1"/></svg>www.myrvbonecare.example</li>
    </ul>
  </div>

  <div class="front-mark">
    <svg viewBox="0 0 140 140" aria-hidden="true">
      <circle cx="70" cy="70" r="67" fill="none" stroke="var(--gold)" stroke-width="1.5"/>
    </svg>
    <p class="front-mark__name">RV Bone &amp; Vitality Center</p>
  </div>

  <div class="social" aria-label="Social profiles">
    <span></span><span></span><span></span>
  </div>
</section>

</body>
</html>
```